Concierge Healthcare Business Card Design and Logo

We need a logo and business card design for a new company called "Sound Haven". We will provide concierge audiological care, hearing aids, hearing exams, custom hearing protection etc to patients in the comfort of their homes and offices. We would like a sleek and modern design preferably with an Ear related logo.

Target Market(s)

People with hearing loss, Hunters, Musicians
My usual clientele are older individuals so usually 50+ years old

Industry/Entity Type

Health Care

Contact Information for Business Card

Celia Brandt, AuD
Audiologist
512-648-2917
soundhaven@mailvoro.com
www.soundhaven-vorel.com

Logo Text

Sound Haven

Number of Pages Required

3 page

```html
<!DOCTYPE html>
<html lang="en">
<head>
<meta charset="utf-8">
<title>Sound Haven — Business Card</title>
<link rel="stylesheet" href="https://fonts.googleapis.com/css2?family=Montserrat:wght@400;500;600&display=swap">
<style>
  :root {
    --page-bg: #2b2b2d;
    --card-bg: #050505;
    --accent: #1fa8e1;
    --white: #ffffff;
    --muted: #d9d9d9;
  }
  * { margin: 0; padding: 0; box-sizing: border-box; }
  html, body { width: 1200px; height: 900px; overflow: hidden; }
  body {
    background: var(--page-bg);
    font-family: "Montserrat", sans-serif;
    position: relative;
  }
  .card {
    position: absolute;
    width: 560px;
    height: 320px;
    left: 320px;
    background: var(--card-bg);
    border-radius: 18px;
    overflow: hidden;
    box-shadow: 0 14px 30px rgba(0,0,0,.45);
  }
  .card-back { top: 100px; }
  .card-front { top: 480px; }

  /* Back */
  .back-brand {
    position: absolute; left: 0; right: 0; top: 92px;
    display: flex; align-items: center; justify-content: center; gap: 16px;
  }
  .brand-dot {
    width: 54px; height: 54px; border-radius: 50%;
    border: 5px solid var(--accent);
  }
  .back-brand .brand-name {
    color: var(--white); font-weight: 600; font-size: 38px; letter-spacing: 4px;
    text-transform: uppercase;
  }
  .back-url {
    position: absolute; left: 0; right: 0; bottom: 52px; text-align: center;
    color: var(--white); font-size: 17px; font-weight: 400; letter-spacing: .5px;
  }

  /* Front */
  .front-shapes { position: absolute; inset: 0; }
  .front-brand {
    position: absolute; left: 26px; top: 34px;
    display: flex; align-items: center; gap: 14px;
  }
  .front-brand .brand-dot { width: 46px; height: 46px; border-width: 4px; }
  .brand-divider { width: 1px; height: 62px; background: var(--muted); }
  .front-brand .brand-name {
    color: var(--white); font-weight: 600; font-size: 22px; line-height: 1.15;
    letter-spacing: 3px; text-transform: uppercase;
  }
  .person {
    position: absolute; right: 28px; top: 92px; text-align: right;
  }
  .person-name { color: var(--accent); font-weight: 600; font-size: 20px; }
  .person-role { color: var(--white); font-size: 13px; margin-top: 2px; }
  .contacts {
    position: absolute; left: 30px; top: 214px; list-style: none;
  }
  .contacts li {
    display: flex; align-items: center; gap: 10px;
    color: var(--white); font-size: 14px; line-height: 20px;
  }
  .contacts svg { width: 12px; height: 12px; flex: none; }
</style>
</head>
<body>

<section class="card card-back" aria-label="Business card back">
  <div class="back-brand">
    <span class="brand-dot"></span>
    <span class="brand-name">Sound Haven</span>
  </div>
  <p class="back-url">www.soundhaven-vorel.com</p>
</section>

<section class="card card-front" aria-label="Business card front">
  <svg class="front-shapes" viewBox="0 0 560 320" aria-hidden="true">
    <circle cx="250" cy="200" r="150" fill="none" stroke="#1fa8e1" stroke-opacity=".12" stroke-width="14"/>
    <line x1="200" y1="146" x2="560" y2="146" stroke="#1fa8e1" stroke-width="1.5"/>
    <line x1="0" y1="206" x2="340" y2="206" stroke="#1fa8e1" stroke-width="1.5"/>
    <polygon points="0,290 345,280 330,320 0,320" fill="#ffffff"/>
    <polygon points="360,240 560,232 560,320 340,320" fill="#1fa8e1"/>
  </svg>

  <div class="front-brand">
    <span class="brand-dot"></span>
    <span class="brand-divider"></span>
    <span class="brand-name">Sound<br>Haven</span>
  </div>

  <div class="person">
    <p class="person-name">Celia Brandt, AuD</p>
    <p class="person-role">Audiologist</p>
  </div>

  <ul class="contacts">
    <li>
      <svg viewBox="0 0 24 24"><path fill="#1fa8e1" d="M6.6 10.8a15.1 15.1 0 0 0 6.6 6.6l2.2-2.2c.3-.3.7-.4 1-.2 1.1.4 2.3.6 3.6.6.6 0 1 .4 1 1V20c0 .6-.4 1-1 1A17 17 0 0 1 3 4c0-.6.4-1 1-1h3.5c.6 0 1 .4 1 1 0 1.3.2 2.5.6 3.6.1.3 0 .7-.2 1z"/></svg>
      512-648-2917
    </li>
    <li>
      <svg viewBox="0 0 24 24"><rect x="2" y="5" width="20" height="14" rx="2" fill="none" stroke="#1fa8e1" stroke-width="2"/><path d="M3 6l9 7 9-7" fill="none" stroke="#1fa8e1" stroke-width="2"/></svg>
      soundhaven@mailvoro.com
    </li>
    <li>
      <svg viewBox="0 0 24 24"><circle cx="12" cy="12" r="10" fill="none" stroke="#1fa8e1" stroke-width="2"/><path d="M2 12h20M12 2c3 3 3 17 0 20M12 2c-3 3-3 17 0 20" fill="none" stroke="#1fa8e1" stroke-width="2"/></svg>
      www.soundhaven-vorel.com
    </li>
  </ul>
</section>

</body>
</html>
```